Business Card Design Can you design a business card design? Looking for something unique and differe

Can you design a business card design? Looking for something unique and different. Can you design a business card design? Looking for something unique and different.Can you design a business card design? Looking for something unique and different.Can you design a business card design? Looking for something unique and different.Can you design a business card design? Looking for something unique and different.Can you design a business card design? Looking for something unique and different.

Industry/Entity Type

Business

Contact Information for Business Card

Can you design a business card design? Looking for something unique and different.

Font styles to use
Serif

```html
<!DOCTYPE html>
<html lang="en">
<head>
<meta charset="utf-8">
<title>Dosewell – Business Card</title>
<link rel="stylesheet" href="https://fonts.googleapis.com/css2?family=Baloo+2:wght@500&family=Open+Sans:ital,wght@0,400;1,400&display=swap">
<style>
  :root {
    --page-bg: #e6e1da;
    --card-light: #f7f5f3;
    --card-mid: #ebe7e4;
    --ink-dark: #0d0c0e;
    --brand-purple: #6f5a82;
    --accent-purple: #7d6192;
    --band-grey: #77727a;
    --text-grey: #5f5a62;
    --contact-sand: #cbb99c;
    --icon-grey: #9b949c;
  }
  * { box-sizing: border-box; margin: 0; padding: 0; }
  html, body {
    width: 1200px; height: 970px; overflow: hidden;
    background: var(--page-bg);
  }
  .business-card {
    position: absolute; left: 172px; top: 248px;
    width: 856px; height: 475px;
    background: linear-gradient(160deg, var(--card-light), var(--card-mid));
    border: 1px solid #d8d3ce;
    box-shadow: 0 14px 36px rgba(0,0,0,0.16);
    overflow: hidden;
    font-family: "Open Sans", Arial, sans-serif;
  }
  .card-waves { position: absolute; inset: 0; width: 856px; height: 475px; }
  .brand-block {
    position: absolute; left: 40px; top: 225px; width: 410px;
    text-align: center;
  }
  .brand-name {
    display: inline-flex; align-items: center; gap: 14px;
    font-family: "Baloo 2", Arial, sans-serif; font-weight: 500;
    font-size: 58px; line-height: 1; color: var(--brand-purple);
  }
  .brand-square { width: 22px; height: 22px; background: var(--brand-purple); }
  .brand-tagline {
    display: flex; align-items: center; justify-content: center; gap: 10px;
    margin-top: 8px;
    font-size: 14px; letter-spacing: 3.2px; color: var(--text-grey);
  }
  .brand-tagline::before, .brand-tagline::after {
    content: ""; width: 38px; height: 1px; background: var(--text-grey);
  }
  .person {
    position: absolute; right: 40px; top: 50px; text-align: right;
  }
  .person-name {
    font-family: "Baloo 2", Arial, sans-serif; font-weight: 500;
    font-size: 27px; line-height: 1.1; color: var(--brand-purple);
  }
  .person-title {
    margin-top: 6px; font-style: italic; font-size: 16px; color: #222;
  }
  .contact-list {
    position: absolute; right: 36px; top: 312px; list-style: none;
  }
  .contact-item {
    display: flex; align-items: center; justify-content: flex-end; gap: 12px;
    height: 28px; font-size: 18px; color: var(--contact-sand);
  }
  .contact-item svg { width: 17px; height: 17px; fill: var(--icon-grey); flex: none; }
</style>
</head>
<body>
  <div class="business-card">
    <svg class="card-waves" viewBox="0 0 856 475" aria-hidden="true">
      <path d="M0,366 C150,378 330,442 520,378 L522,394 C330,452 150,404 0,420 Z" fill="var(--band-grey)" opacity="0.85"/>
      <path d="M856,218 C700,224 560,300 420,378 C320,432 160,432 0,426 L0,475 L856,475 Z" fill="var(--ink-dark)"/>
      <path d="M856,206 C690,210 560,282 430,352 C330,402 200,402 90,386" fill="none" stroke="var(--accent-purple)" stroke-width="6" stroke-linecap="round"/>
    </svg>

    <div class="brand-block">
      <div class="brand-name"><span class="brand-square"></span>Dosewell</div>
      <div class="brand-tagline">cost management</div>
    </div>

    <div class="person">
      <div class="person-name">Your Long Name</div>
      <div class="person-title">Managing Director</div>
    </div>

    <ul class="contact-list">
      <li class="contact-item">00.00.00.0000
        <svg viewBox="0 0 16 16"><path d="M2 5c0-2 2-3 6-3s6 1 6 3v1h-3V5H5v1H2zM4 7h8l2 6H2z"/></svg></li>
      <li class="contact-item">00.00.00.0000
        <svg viewBox="0 0 16 16"><path d="M4 1h8v4H4zM2 6h12v6h-2v3H4v-3H2zM5 10v4h6v-4z"/></svg></li>
      <li class="contact-item">www.yourwebsite.com
        <svg viewBox="0 0 16 16"><path d="M8 1a7 7 0 1 0 0 14A7 7 0 0 0 8 1zm0 1.5c.8 0 1.7 1.5 2 4.5H6c.3-3 1.2-4.5 2-4.5zM2.6 7h2c0-1.6.3-3 .8-3.9A5.5 5.5 0 0 0 2.6 7zm8.8 0h2a5.5 5.5 0 0 0-2.8-3.9c.5.9.8 2.3.8 3.9zM2.6 9a5.5 5.5 0 0 0 2.8 3.9c-.5-.9-.8-2.3-.8-3.9zm3.4 0c.3 3 1.2 4.5 2 4.5s1.7-1.5 2-4.5zm5.4 0c0 1.6-.3 3-.8 3.9A5.5 5.5 0 0 0 13.4 9z"/></svg></li>
      <li class="contact-item">yourname@yourwebsite.com
        <svg viewBox="0 0 16 16"><path d="M1 3h14v10H1zm1.5 1.5L8 9l5.5-4.5z"/></svg></li>
      <li class="contact-item">Your Commercial or office address
        <svg viewBox="0 0 16 16"><path d="M8 1a5 5 0 0 0-5 5c0 4 5 9 5 9s5-5 5-9a5 5 0 0 0-5-5zm0 7a2 2 0 1 1 0-4 2 2 0 0 1 0 4z"/></svg></li>
    </ul>
  </div>
</body>
</html>
```